Business Card Design

We are looking for a business card designed for our landscaping company. We do landscaping installation & Maintenance Services. We would like to see designs that have basic landscaping in background. We also think it is important to have both of our names and phone numbers on the card. We need something that stands out a little whether it is shape of the card or thickness or design.

Business

Bramblewood Yardworks, bramblewoodyard@mailvista.net, Owen Platt 555-273-9104, Daniel Korbin 555-618-3927

```html
<!DOCTYPE html>
<html lang="en">
<head>
<meta charset="utf-8">
<title>Bramblewood Yardworks – Business Card</title>
<link href="https://fonts.googleapis.com/css2?family=Open+Sans:wght@400;600;700&display=swap" rel="stylesheet">
<style>
  :root {
    --panel-lime: #cff07c;
    --brand-green: #27e02a;
    --text-dark: #1e1e1e;
    --garden-deep: #2f6d1e;
    --garden-mid: #5ea83a;
    --garden-light: #9fd35a;
    --bloom-red: #c8323c;
    --bloom-pink: #d66aa0;
    --path-stone: #d9dccd;
    --page-bg: #ffffff;
  }
  html, body {
    margin: 0;
    padding: 0;
    overflow: hidden;
    background: var(--page-bg);
  }
  .card {
    position: relative;
    width: 1200px;
    height: 703px;
    overflow: hidden;
    font-family: "Open Sans", sans-serif;
  }
  .card-art {
    position: absolute;
    inset: 0;
    display: block;
  }
  .brand-name {
    position: absolute;
    left: 70px;
    top: 168px;
    margin: 0;
    font-size: 64px;
    line-height: 74px;
    font-weight: 700;
    color: var(--brand-green);
    text-shadow: 0 0 2px #fff, 0 0 2px #fff, 0 0 3px #fff;
    letter-spacing: -0.5px;
  }
  .contacts {
    position: absolute;
    left: 70px;
    top: 406px;
    margin: 0;
    padding: 0;
    list-style: none;
    font-size: 29px;
    line-height: 50px;
    font-weight: 600;
    color: var(--text-dark);
  }
  .contacts .person {
    display: inline-block;
    margin-right: 22px;
  }
  .email {
    position: absolute;
    left: 70px;
    top: 596px;
    margin: 0;
    font-size: 29px;
    font-weight: 600;
    color: var(--text-dark);
  }
</style>
</head>
<body>
  <div class="card">
    <svg class="card-art" width="1200" height="703" viewBox="0 0 1200 703">
      <defs>
        <linearGradient id="garden-tone" x1="0" y1="0" x2="1" y2="1">
          <stop offset="0" stop-color="var(--garden-mid)"/>
          <stop offset="0.35" stop-color="var(--garden-light)"/>
          <stop offset="0.6" stop-color="var(--garden-mid)"/>
          <stop offset="1" stop-color="var(--garden-deep)"/>
        </linearGradient>
        <radialGradient id="bloom-tone" cx="0.62" cy="0.68" r="0.45">
          <stop offset="0" stop-color="var(--bloom-red)" stop-opacity="0.55"/>
          <stop offset="0.6" stop-color="var(--bloom-pink)" stop-opacity="0.25"/>
          <stop offset="1" stop-color="var(--bloom-pink)" stop-opacity="0"/>
        </radialGradient>
      </defs>
      <g role="img" aria-label="Photo of a landscaped garden with flower beds, shaped shrubs and a winding stone path">
        <rect x="0" y="0" width="1200" height="703" fill="url(#garden-tone)"/>
        <rect x="0" y="0" width="1200" height="703" fill="url(#bloom-tone)"/>
      </g>
      <path class="text-panel" d="M0 0 H442 C640 120 860 330 884 703 H0 Z" fill="var(--panel-lime)"/>
    </svg>

    <h1 class="brand-name">Bramblewood<br>Yardworks</h1>

    <ul class="contacts">
      <li><span class="person">Owen Platt</span>555-273-9104,</li>
      <li><span class="person">Daniel Korbin</span>555-618-3927</li>
    </ul>

    <p class="email">bramblewoodyard@mailvista.net</p>
  </div>
</body>
</html>
```